Fine Art business needs new website

We need a simple website with a home page, about us page, New sculptures, Sold sculptures, and a contact us page.Our sculptures are very high end one of a kind pieces. As such we need the site to be VERY elegant and professional. Lastly, because I'll be updating pictures on the website on a monthly basis it needs to be user friendly to update (Wordpress is preferred). The only branding we have so far for the business is a business card.
Updates
I wasn't completely ready when this project launched, also I am on the road right now and haven't been able to be as responsive to all you designers as I would like. I will work on giving feedback to all the top designs we've received so far. Thank you all so much for your participation and hardwork.
Target Market(s)
High end customers (affluent), art collectors, interior decorators/designers
Industry/Entity Type
Art Gallery
Coding
Coded - Design and coding required
Number of Pages Required
5+ page
Requirements
Must have
- Easily editable picture gallery for myself so that I can add new pieces(pictures of the pieces), remove sold pieces, etc. I would like the website to be built in wordpress so I can update it. I currently use mangewordpress through Netmarro for my other business website and would like to do the same for this one.
- Pages:
- -Intro page with featured pieces
- -Current pieces gallery (for sale) mainly a picture gallery
- -Sculptures archive (sold pieces) another picture gallery
- -About us: Pull-down of -about the artist (attached content)
- -Artistic Process (attached content)
- -Show Schedule:
- -one page dedicated to "friends of TMV" (basically a link page)
- TO BE CLEAR "www.pineroverslane.com" IS A TOTALLY DIFFERENT SITE AND I'M NOT TRYING TO COMBINE THE TWO OR JOIN THEM INTO ONE. This page needs be more elegant and seperate from the Pine Rovers site.
- UPDATE: I'd like a link to the TMV Faceplume page: https://www.faceplume-social.com/mirelcraftworks/
Nice to have
- I would like the pictures on the gallery pages able to have text connected with them (Materials, price)
- I would like the site style and fonts to be similar to our business cards we've already had designed (picture attached).
Should not have
- Too much flash or other things that will make the site slow to load.

```html
<!DOCTYPE html>
<html lang="en">
<head>
<meta charset="utf-8">
<title>Terra Mira Vault</title>
<link href="https://fonts.googleapis.com/css2?family=Cormorant+Garamond:wght@400;500&family=Karla:wght@400;500;700&family=Tinos:wght@400;700&display=swap" rel="stylesheet">
<style>
  :root {
    --ink: #111111;
    --body-text: #555555;
    --accent-dot: #3a1fb0;
    --band-left: #dcedf4;
    --band-right: #b6bfe8;
    --lavender: #9b9fd6;
    --mist: #d6e0e6;
    --amethyst: #4a2a8a;
    --gold-stone: #a49472;
    --white: #ffffff;
  }
  * { margin: 0; padding: 0; box-sizing: border-box; }
  html, body { width: 1200px; height: 1000px; overflow: hidden; background: var(--white); }
  body { position: relative; font-family: "Karla", sans-serif; color: var(--ink); }

  .site-header { position: absolute; top: 0; left: 0; width: 1200px; height: 72px; }
  .brand { position: absolute; left: 158px; top: 22px; font-family: "Cormorant Garamond", serif; font-size: 23px; letter-spacing: 0.5px; color: #333; text-transform: uppercase; }
  .main-nav { position: absolute; left: 440px; top: 28px; display: flex; gap: 18px; font-size: 14px; letter-spacing: 0.3px; }
  .main-nav a { color: var(--ink); text-decoration: none; }

  .hero-ring { position: absolute; left: 0; top: 0; width: 1200px; height: 600px; }
  .hero-band { position: absolute; left: 0; top: 207px; width: 1200px; height: 252px; background: linear-gradient(90deg, var(--band-left) 0%, var(--band-left) 20%, var(--band-right) 60%); }
  .hero-photo { position: absolute; left: 440px; top: 207px; width: 760px; height: 252px;
    background: linear-gradient(100deg, rgba(74,42,138,0) 0%, var(--amethyst) 12%, #5b3da8 38%, var(--gold-stone) 52%, #8c7c5c 70%, var(--amethyst) 90%, var(--lavender) 100%); }
  .hero-title { position: absolute; left: 158px; top: 168px; font-family: "Cormorant Garamond", serif; font-weight: 400; font-size: 76px; line-height: 83px; letter-spacing: 1px; text-transform: uppercase; }
  .hero-contact { position: absolute; left: 160px; top: 343px; display: flex; gap: 14px; font-size: 14.5px; color: #444; }
  .hero-contact span { display: flex; align-items: center; gap: 5px; }
  .hero-cta { position: absolute; left: 270px; top: 393px; width: 158px; height: 31px; border: 1.5px solid var(--ink); font-size: 10px; letter-spacing: 1.5px; display: flex; align-items: center; justify-content: center; color: var(--ink); text-decoration: none; text-transform: uppercase; }

  .feature { position: absolute; left: 0; top: 592px; width: 1200px; height: 378px; }
  .feature-photo { position: absolute; left: 0; top: 0; width: 600px; height: 378px; background: linear-gradient(150deg, var(--lavender) 0%, #b6b9dc 50%, var(--mist) 100%); }
  .feature-info { position: absolute; left: 634px; top: 22px; width: 470px; }
  .feature-title { font-family: "Cormorant Garamond", serif; font-weight: 500; font-size: 40px; line-height: 48px; }
  .feature-label { font-size: 14.5px; font-weight: 700; margin-top: 18px; }
  .feature-text { font-family: "Tinos", serif; font-size: 14.5px; line-height: 18.5px; color: var(--body-text); margin-top: 14px; }
  .feature-label.materials { margin-top: 16px; }
  .feature-price { font-family: "Tinos", serif; font-weight: 700; font-size: 23px; margin-top: 20px; }

  .next-strip { position: absolute; left: 600px; top: 970px; width: 600px; height: 30px; background: linear-gradient(90deg, var(--mist), var(--lavender)); }
</style>
</head>
<body>
  <header class="site-header">
    <div class="brand">Terra Mira Vault</div>
    <nav class="main-nav">
      <a href="#">Gallery</a>
      <a href="#">Archive</a>
      <a href="#">About</a>
      <a href="#">Artistic Process</a>
      <a href="#">Show Schedule</a>
      <a href="https://www.faceplume-social.com/mirelcraftworks/">Faceplume</a>
      <a href="#">Friends of TMV</a>
    </nav>
  </header>

  <svg class="hero-ring" viewBox="0 0 1200 600" aria-hidden="true">
    <circle cx="292" cy="315" r="210" fill="none" stroke="var(--accent-dot)" stroke-width="2" stroke-dasharray="1 3.5" stroke-linecap="round"/>
  </svg>
  <div class="hero-band"></div>
  <div class="hero-photo" role="img" aria-label="Large amethyst geode arch sculpture with golden stone rim"></div>

  <h1 class="hero-title">Terra Mira<br>Vault</h1>
  <div class="hero-contact">
    <span>
      <svg width="10" height="12" viewBox="0 0 10 12" aria-hidden="true"><path d="M2 0.5 L4 3 L3 4.5 C3.5 6.5 4.5 8 6 9 L7.5 8 L9.8 10 L8.5 11.6 C4 11 0.5 6 0.4 2 Z" fill="#444"/></svg>
      (970) 555-0148
    </span>
    <span>
      <svg width="13" height="10" viewBox="0 0 13 10" aria-hidden="true"><rect x="0.5" y="0.5" width="12" height="9" fill="#444"/><path d="M0.5 0.8 L6.5 5.5 L12.5 0.8" fill="none" stroke="#fff" stroke-width="1"/></svg>
      wren@pineroverslane.com
    </span>
  </div>
  <a class="hero-cta" href="#">Explore Gallery</a>

  <section class="feature">
    <div class="feature-photo" role="img" aria-label="Mounted amethyst geode cluster on a stand"></div>
    <div class="feature-info">
      <h2 class="feature-title">Amethyst Geode Mounted</h2>
      <p class="feature-label">Product Story:</p>
      <p class="feature-text">Lorem ipsum dolor sit amet, consectetur adipisicing elit, sed do eiusmod tempor incididunt ut labore et dolore magna aliqua. Ut enim ad minim veniam, quis nostrud exercitation ullamco laboris nisi ut aliquip ex ea commodo consequat. Duis aute irure dolor in reprehenderit in voluptate velit</p>
      <p class="feature-label materials">Materials:</p>
      <p class="feature-text">Amethyst Crystal, Gold Mounting Plates, Kauri Wood Base</p>
      <p class="feature-price">$1299.00</p>
    </div>
  </section>
  <div class="next-strip"></div>
</body>
</html>
```